Marlowe Crest Realty business card design

Looking for an upscale and clean business card design and updated logo. I sell to a very high-end south Florida real estate market.
Target Market(s)
High-end real estate in south Florida real estate market
Industry/Entity Type
Real Estate Agent
Contact Information for Business Card
Marlowe Crest Realty, Inc
738 West Pinecrest Ave, Suite 410/510, Fort Lauderdale, FL 33308
Gary Whitlock - Broker/Owner
954-327-8846 Direct
garyshomes@quellmail.com
Website: DwellTarrowBay.com
Font styles to use
Other font styles liked:
- Copperplate Gothic, Georgia, etc.
Requirements
Must have
- My photo, company name, my name and title, all info stated in Details above
Nice to have
- Luxury home design element, waterfront

```html
<!DOCTYPE html>
<html lang="en">
<head>
<meta charset="utf-8">
<title>Marlowe Crest Realty – Business Card</title>
<link rel="stylesheet" href="https://fonts.googleapis.com/css2?family=Gelasio:wght@400;700&display=swap">
<style>
  :root {
    --backdrop: #e4e4e2;
    --card-white: #ffffff;
    --sun-gold: #f4b72a;
    --sun-gold-light: #f7c93e;
    --ink: #1c1c1c;
    --ink-soft: #4a4a4a;
    --card-dark: #232323;
    --card-dark-edge: #474747;
    --silver: #c4c4c4;
    --photo-top: #c9c7c2;
    --photo-bottom: #2f4a85;
  }
  * { box-sizing: border-box; margin: 0; padding: 0; }
  html, body {
    width: 1200px; height: 1200px; overflow: hidden;
    background: var(--backdrop);
    font-family: "Gelasio", Georgia, serif;
  }
  .canvas { position: relative; width: 1200px; height: 1200px; }

  .card {
    position: absolute; left: 262px; width: 686px; height: 392px;
    border-radius: 20px; overflow: hidden;
  }
  .card--front { top: 165px; background: var(--card-white); }
  .card--back {
    top: 653px;
    background: linear-gradient(135deg, var(--card-dark) 35%, var(--card-dark-edge) 100%);
  }

  .brand { position: absolute; display: flex; align-items: center; }
  .brand__dot { border-radius: 50%; background: var(--sun-gold); flex: none; }
  .brand__name { white-space: nowrap; font-weight: 400; }

  .card--front .brand { left: 52px; top: 90px; gap: 14px; }
  .card--front .brand__dot { width: 56px; height: 56px; }
  .card--front .brand__name { font-size: 18px; color: var(--ink); }

  .contact { position: absolute; left: 56px; font-size: 14px; color: var(--ink-soft); line-height: 17.5px; }
  .contact__row { display: flex; align-items: flex-start; gap: 7px; }
  .contact__icon { width: 11px; height: 11px; margin-top: 3px; flex: none; fill: var(--sun-gold); }
  .contact__icon--blank { visibility: hidden; }
  .contact--address { top: 230px; }
  .contact--reach { top: 294px; }

  .portrait {
    position: absolute; left: 454px; top: 69px; width: 159px; height: 203px;
    border-radius: 12px;
    background: linear-gradient(180deg, var(--photo-top) 0%, #9c8f88 45%, var(--photo-bottom) 100%);
  }
  .agent { position: absolute; left: 421px; width: 220px; top: 296px; text-align: center; }
  .agent__name { font-size: 24px; font-weight: 700; color: var(--sun-gold); letter-spacing: 0.5px; line-height: 28px; }
  .agent__title { font-size: 15px; color: var(--ink); line-height: 18px; }

  .gold-band {
    position: absolute; left: 0; bottom: 0; width: 100%; height: 12px;
    background: linear-gradient(90deg, var(--sun-gold) 0%, var(--sun-gold-light) 100%);
  }

  .card--back .brand { left: 120px; top: 136px; gap: 20px; }
  .card--back .brand__dot { width: 120px; height: 120px; }
  .card--back .brand__name { font-size: 26px; color: var(--silver); }
</style>
</head>
<body>
<main class="canvas">

  <section class="card card--front" aria-label="Business card front">
    <div class="brand">
      <span class="brand__dot"></span>
      <span class="brand__name">Marlowe Crest Realty, Inc.</span>
    </div>

    <div class="contact contact--address">
      <div class="contact__row">
        <svg class="contact__icon" viewBox="0 0 12 12"><path d="M6 0a4 4 0 0 0-4 4c0 3 4 8 4 8s4-5 4-8a4 4 0 0 0-4-4zm0 5.6A1.6 1.6 0 1 1 6 2.4a1.6 1.6 0 0 1 0 3.2z"/></svg>
        <span>738 West Pinecrest Ave</span>
      </div>
      <div class="contact__row"><svg class="contact__icon contact__icon--blank" viewBox="0 0 12 12"></svg><span>Suite 410/510</span></div>
      <div class="contact__row"><svg class="contact__icon contact__icon--blank" viewBox="0 0 12 12"></svg><span>Fort Lauderdale, FL 33308</span></div>
    </div>

    <div class="contact contact--reach">
      <div class="contact__row">
        <svg class="contact__icon" viewBox="0 0 12 12"><path d="M2.4 0.5l2 2-1 1.5c.8 1.8 2.3 3.3 4.1 4.1l1.5-1 2 2-1.3 2.4C5.2 11.2.8 6.8.5 1.8z"/></svg>
        <span>954-327-8846</span>
      </div>
      <div class="contact__row">
        <svg class="contact__icon" viewBox="0 0 12 12"><path d="M0 2h12v8H0zm1 1 5 3.5L11 3z" fill-rule="evenodd"/></svg>
        <span>garyshomes@quellmail.com</span>
      </div>
      <div class="contact__row">
        <svg class="contact__icon" viewBox="0 0 12 12"><path d="M6 0a6 6 0 1 0 0 12A6 6 0 0 0 6 0zm0 1.2a4.8 4.8 0 0 1 0 9.6 4.8 4.8 0 0 1 0-9.6zM3 5h6v2H3z"/></svg>
        <span>DwellTarrowBay.com</span>
      </div>
    </div>

    <div class="portrait" role="img" aria-label="Portrait photo of Gary Whitlock, broker and owner"></div>

    <div class="agent">
      <p class="agent__name">GARY WHITLOCK</p>
      <p class="agent__title">Broker/Owner</p>
    </div>

    <div class="gold-band"></div>
  </section>

  <section class="card card--back" aria-label="Business card back">
    <div class="brand">
      <span class="brand__dot"></span>
      <span class="brand__name">Marlowe Crest Realty, Inc.</span>
    </div>
  </section>

</main>
</body>
</html>
```